wordpress website Carla Winfield, Author, Speaker and Coach

Need a wordpress blogging website for author/speaker/coach.
I have paid for hosting on nestparrot.
I am currently writing a book - Launchpad to Campus - Steps and strategies to prepare you to thrive in college and beyond. Eventually, I will have an Academic/Life Coaching program targeting high school and college students. This website's purpose is to build my email list. I can offer the following reports as incentive for email sign-up:
1. Six Habits That Get Your Teen Through University On Schedule and Debt-Light
2. Surprising Routes to Fund Your Degree
3. SAT/ACT vocabulary word of the day

facebook page: https://www.facebook.com/Carla-Winfield-AcademicLife-Coach-918273645501928/

I would like to have these pages:

1. Home or About page

High school is becoming more and more stressful for students. Not only are they taking more AP classes than ever before, and often spending $1,000’s on SAT/ACT prep programs, most are NOT prepared for success in college. Only 19% of students are graduating from college within 4 years and only 56% are graduating within 6 years. With the cost of higher education skyrocketing, each extra year of school can costs families $40,000 - $60,000 when you factor in living expenses. Then, when students do graduate, they are often underemployed.

Carla's approach is whole person oriented. Her programs help students learn life skills in addition to the study, time management skills, etc. offered by most academic coaching programs. Our program addresses all of the major causes of failure to graduate within 4 years, and is based on sound educational research. Carla's program initially provides the daily interaction needed to successfully change behaviors and seat new success habits, unlike many programs in which students interact with coaches only once a week.
Bio
Carla Winfield is a certified teacher and holds advanced certification in academic coaching and tutoring. She also is a certified trainer in the Morris Tellwright Achievement Keys. She has three successful adult children, and helped them overcome learning differences and thrive.

2. Blog

3. Contact - Include form (I split time between USA and Saudi Arabia, so I will call or email people back, but don't want to leave a phone number)
info@carlawinfield.example

4. Store – 1 book for now
Launchpad to Campus
Steps and strategies to prepare you to thrive in college and beyond
Available 12/01/2017
I could make a preview chapter available for download

5. Speaking
Carla Winfield is available for keynote addresses and half-day, full day or multi-day workshops. I will develop details later

6.Coaching programs
I will develop details later

Target Market(s)

high school students who are college bound and their parents

Number of Pages Required

5+ page

Font styles to use
Sans Serif

Colors

Designer to choose colors to be used in the design.

Requirements
Nice to have
• integration with post finch for contact management

```html
<!DOCTYPE html>
<html lang="en">
<head>
<meta charset="utf-8">
<title>Carla Winfield – Author, Speaker and Coach</title>
<link rel="stylesheet" href="https://fonts.googleapis.com/css2?family=Montserrat:wght@500;600;700&family=Open+Sans:ital,wght@0,400;0,600;0,700;1,400&display=swap">
<style>
:root{
  --green:#7dc142;
  --lavender:#9c9ad4;
  --ink:#222327;
  --body:#6b6b6b;
  --meta:#8a8a9a;
  --footer:#15161e;
  --white:#ffffff;
  --line:#e2e2e2;
  --sunset-top:#4a3d3a;
  --sunset-mid:#c7792c;
  --sunset-low:#3a2a1c;
}
*{box-sizing:border-box;margin:0;padding:0}
html,body{width:1200px;height:2500px;overflow:hidden}
body{font-family:"Open Sans",Arial,sans-serif;color:var(--body);background:var(--white);position:relative}
h1,h2,h3,.brand,.nav a{font-family:"Montserrat",Arial,sans-serif}
.wrap{position:absolute;left:97px;width:1006px}

/* Hero */
.hero{position:absolute;top:0;left:0;width:1200px;height:533px;overflow:hidden;border-top:4px solid var(--green);
  background:linear-gradient(180deg,var(--sunset-top) 0%,#8a5a35 30%,var(--sunset-mid) 55%,#9a5a22 78%,var(--sunset-low) 100%)}
.hero-scene{position:absolute;inset:0;background:radial-gradient(ellipse 520px 260px at 620px 330px,rgba(255,214,130,.55),rgba(255,214,130,0) 70%)}
.topbar{position:absolute;top:0;left:0;width:1200px;height:92px;border-bottom:1px solid rgba(255,255,255,.35);background:rgba(0,0,0,.25)}
.brand{position:absolute;left:97px;top:24px;display:flex;align-items:center;gap:12px;color:var(--white);font-size:20px;font-weight:600}
.brand-dot{width:38px;height:38px;border-radius:50%;border:2px solid var(--green)}
.nav{position:absolute;right:97px;top:32px;display:flex;gap:27px;align-items:center}
.nav a{color:var(--white);text-decoration:none;font-size:17px;font-weight:500}
.nav a.active{color:var(--green)}
.hero-title{position:absolute;left:97px;top:165px;color:var(--white);font-size:50px;font-weight:600;letter-spacing:.5px}
.hero-lede{position:absolute;left:97px;top:232px;width:560px;color:var(--white);font-size:16.5px;font-weight:600;line-height:26px}
.signup{position:absolute;left:97px;top:303px;display:flex}
.signup input{width:400px;height:48px;border:0;padding:0 14px;font:14px "Open Sans",sans-serif;color:#888}
.signup button{width:140px;height:48px;border:0;background:var(--green);color:var(--white);font:700 16px "Open Sans",sans-serif}
.reports{position:absolute;left:97px;top:372px;list-style:none;color:#f1e8dc;font-style:italic;font-size:15px;line-height:30px}
.dots{position:absolute;left:572px;top:469px;display:flex;gap:7px}
.dots span{width:11px;height:11px;border-radius:50%;border:1.5px solid var(--white)}
.dots span.on{background:var(--white)}
.book{position:absolute;left:780px;top:138px;width:245px;height:360px;border-radius:3px 6px 6px 3px;
  background:linear-gradient(100deg,#3a3150 0%,#6a5f82 45%,#4b405f 100%);box-shadow:8px 0 0 #1b1b1f,12px 6px 18px rgba(0,0,0,.5)}

/* About */
.about{position:absolute;top:533px;left:0;width:1200px;height:617px}
.portrait{position:absolute;left:97px;top:84px;width:368px;height:453px;border:5px solid var(--white);box-shadow:0 0 0 1px var(--line);
  background:linear-gradient(160deg,#3a2d2a 0%,#1a1514 60%,#b08a2c 100%)}
.about-text{position:absolute;left:535px;top:80px;width:568px}
.about-text h2{color:var(--ink);font-size:32px;font-weight:600;margin-bottom:30px}
.about-text p{font-size:13px;line-height:27px;margin-bottom:26px}
.badge{position:absolute;left:530px;top:387px;width:142px;height:142px;border-radius:50%;
  background:radial-gradient(circle at 40% 35%,#f2f2f2,#a9a9a9 70%,#8a8a8a);box-shadow:0 0 0 4px #d8d8d8}

/* Coaching */
.coaching{position:absolute;top:1150px;left:0;width:1200px;height:447px;background:linear-gradient(90deg,#a4a2da 0%,var(--lavender) 50%,#9896d0 100%)}
.coaching h2{position:absolute;left:97px;top:58px;color:var(--white);font-size:31px;font-weight:500}
.coaching-text{position:absolute;left:97px;top:122px;width:500px;color:var(--white);font-size:13px;line-height:25px}
.coaching-text p{margin-bottom:22px}
.btn-green{position:absolute;left:97px;top:345px;width:145px;height:38px;border:2px solid #9fd86e;background:var(--green);color:var(--white);font:700 13px "Open Sans",sans-serif;display:flex;align-items:center;justify-content:center}
.class-photo{position:absolute;left:658px;top:45px;width:443px;height:355px;border:4px solid var(--white);
  background:linear-gradient(135deg,#6c5a4c 0%,#a88a74 40%,#d79aa8 70%,#7c6655 100%)}

/* Blog */
.blog{position:absolute;top:1597px;left:0;width:1200px;height:661px}
.blog h2{position:absolute;left:0;width:1200px;top:78px;text-align:center;color:var(--ink);font-size:31px;font-weight:600}
.cards{position:absolute;left:97px;top:153px;display:flex;gap:36px}
.card{width:311px}
.card-img{height:185px;border:4px solid var(--white);box-shadow:0 0 0 1px var(--line)}
.img-a{background:linear-gradient(135deg,#f7d24a,#f1a83a 55%,#e47a2c)}
.img-b{background:linear-gradient(135deg,#3a5c8c,#7b8fa8 50%,#c9a48c)}
.img-c{background:linear-gradient(135deg,#8ca66a,#c9b48a 55%,#e0d2b8)}
.card h3{color:var(--ink);font-size:19px;font-weight:600;margin:23px 0 9px}
.meta{display:flex;align-items:center;gap:8px;font-size:11.5px;font-style:italic;color:var(--meta)}
.meta svg{width:11px;height:11px;fill:var(--lavender)}
.card p{font-size:12.5px;line-height:22px;margin-top:12px}
.read-more{display:block;margin-top:14px;color:var(--green);font-size:12.5px;font-weight:700}
.btn-outline{position:absolute;left:514px;top:554px;width:173px;height:39px;border:2px solid #d6d6d6;color:var(--green);font:700 14px "Open Sans",sans-serif;display:flex;align-items:center;justify-content:center}

/* Footer */
.footer{position:absolute;top:2258px;left:0;width:1200px;height:242px;background:var(--footer);border-top:5px solid;border-image:linear-gradient(90deg,#4a5fc0,var(--green)) 1}
.contacts{position:absolute;top:35px;left:0;width:1200px;display:flex;justify-content:center;gap:55px;color:var(--white);font-size:13.5px;line-height:24px}
.contact{display:flex;align-items:center;gap:18px}
.ring{width:43px;height:43px;border-radius:50%;border:1.5px solid var(--white);display:flex;align-items:center;justify-content:center}
.ring svg{width:17px;height:17px;fill:var(--white)}
.foot-nav{position:absolute;top:112px;left:0;width:1200px;text-align:center;color:var(--white);font-size:13.5px}
.foot-nav span{margin:0 10px}
.foot-rule{position:absolute;left:97px;top:163px;width:1006px;border-top:1px solid #333540}
.copyright{position:absolute;left:97px;top:193px;color:var(--white);font-size:12.5px}
.social{position:absolute;right:97px;top:180px;display:flex;gap:8px}
.social span{width:38px;height:38px;border-radius:50%;border:1.5px solid var(--white)}
</style>
</head>
<body>

<header class="hero">
  <div class="hero-scene" role="img" aria-label="Silhouette of a girl with raised arms in a field at sunset with birds flying"></div>
  <div class="topbar"></div>
  <div class="brand"><span class="brand-dot"></span>Carla Winfield</div>
  <nav class="nav">
    <a class="active">Home</a><a>Blog</a><a>Store</a><a>Speaking</a><a>Coaching Program</a><a>Contact</a>
    <svg width="17" height="17" viewBox="0 0 20 20" aria-label="Search"><circle cx="8" cy="8" r="6" fill="none" stroke="#fff" stroke-width="2.6"/><path d="M12.5 12.5 18 18" stroke="#fff" stroke-width="3" stroke-linecap="round"/></svg>
  </nav>
  <h1 class="hero-title">CARLA WINFIELD</h1>
  <p class="hero-lede">I am currently writing a book - Launchpad to Campus - Steps and strategies to prepare you to thrive in college and beyond.</p>
  <form class="signup"><input type="text" value="Email Address" aria-label="Email Address"><button type="button">SIGN-UP</button></form>
  <ol class="reports">
    <li>1. Six Habits That Get Your Teen Through University On Schedule and Debt-Light</li>
    <li>2. Surprising Routes to Fund Your Degree</li>
    <li>3. SAT/ACT vocabulary word of the day</li>
  </ol>
  <div class="dots"><span class="on"></span><span></span><span></span><span></span></div>
  <div class="book" role="img" aria-label="Hardcover book Launchpad to Campus"></div>
</header>

<section class="about">
  <div class="portrait" role="img" aria-label="Portrait photo of Carla Winfield"></div>
  <div class="about-text">
    <h2>I AM CARLA WINFIELD</h2>
    <p>High school is becoming more and more stressful for students. Not only are they taking more AP classes than ever before, and often spending $1,000’s on SAT/ACT prep programs, most are NOT prepared for success in college.</p>
    <p>Only 19% of students are graduating from college within 4 years and only 56% are graduating within 6 years. With the cost of higher education skyrocketing, each extra year of school can costs families $40,000 - $60,000 when you factor in living expenses. Then, when students do graduate, they are often underemployed.</p>
  </div>
  <div class="badge" role="img" aria-label="Morris Tellwright Achievement Keys certified trainer seal"></div>
</section>

<section class="coaching">
  <h2>LIFE COACHING PROGRAM</h2>
  <div class="coaching-text">
    <p>Sed ut perspiciatis unde omnis iste natus error sit voluptatem accusantium dolo remque laudantium, totam rem aperia.</p>
    <p>Eque ipsa quae ab illo inventore veritatis et quasi architecto beatae vitae dicta su nt explicabo. Nemo enim ipsam voluptatem quia voluptas sit aspernatur aut odit aut fugit, sed quia consequuntur magni dolores eos qui ratione voluptatem seui nesciunt. Neque porro quisquam est, qui dolorem ipsum quia dolor sit amet con sectetur, adipisci velit, sed quia non numquam.</p>
  </div>
  <a class="btn-green">READ MORE &gt;&gt;</a>
  <div class="class-photo" role="img" aria-label="Coach speaking to a room of seated students"></div>
</section>

<section class="blog">
  <h2>LATEST BLOG</h2>
  <div class="cards">
    <article class="card">
      <div class="card-img img-a" role="img" aria-label="Young woman stretching in bright sunlight"></div>
      <h3>Finibus Bonorum et Malorum</h3>
      <div class="meta"><svg viewBox="0 0 10 10"><rect x="0" y="1" width="10" height="9" rx="1"/></svg>22/06/2017 <span>|</span><svg viewBox="0 0 10 10"><circle cx="5" cy="3" r="2.6"/><path d="M0 10c0-3 2-4.5 5-4.5S10 7 10 10z"/></svg>Carla Winfield</div>
      <p>Nemo enim ipsam voluptatem quia voluptas siaspern atur aut odit aut fugit, sed quia consequ.</p>
      <a class="read-more">READ MORE &gt;&gt;</a>
    </article>
    <article class="card">
      <div class="card-img img-b" role="img" aria-label="Group of smiling students together"></div>
      <h3>Finibus Bonorum et Malorum</h3>
      <div class="meta"><svg viewBox="0 0 10 10"><rect x="0" y="1" width="10" height="9" rx="1"/></svg>22/06/2017 <span>|</span><svg viewBox="0 0 10 10"><circle cx="5" cy="3" r="2.6"/><path d="M0 10c0-3 2-4.5 5-4.5S10 7 10 10z"/></svg>Carla Winfield</div>
      <p>Nemo enim ipsam voluptatem quia voluptas siaspern atur aut odit aut fugit, sed quia consequ.</p>
      <a class="read-more">READ MORE &gt;&gt;</a>
    </article>
    <article class="card">
      <div class="card-img img-c" role="img" aria-label="Two friends riding bicycles outdoors"></div>
      <h3>Finibus Bonorum et Malorum</h3>
      <div class="meta"><svg viewBox="0 0 10 10"><rect x="0" y="1" width="10" height="9" rx="1"/></svg>22/06/2017 <span>|</span><svg viewBox="0 0 10 10"><circle cx="5" cy="3" r="2.6"/><path d="M0 10c0-3 2-4.5 5-4.5S10 7 10 10z"/></svg>Carla Winfield</div>
      <p>Nemo enim ipsam voluptatem quia voluptas siaspern atur aut odit aut fugit, sed quia consequ.</p>
      <a class="read-more">READ MORE &gt;&gt;</a>
    </article>
  </div>
  <a class="btn-outline">VIEW MORE BLOG</a>
</section>

<footer class="footer">
  <div class="contacts">
    <div class="contact"><span class="ring"><svg viewBox="0 0 20 20"><path d="M10 1a6 6 0 0 0-6 6c0 4.5 6 12 6 12s6-7.5 6-12a6 6 0 0 0-6-6zm0 8.3a2.3 2.3 0 1 1 0-4.6 2.3 2.3 0 0 1 0 4.6z"/></svg></span><span>218 Linden Parkway, 12th Floor<br>Brookfield, NY 10455</span></div>
    <div class="contact"><span class="ring"><svg viewBox="0 0 20 20"><path d="M4 1.5 7 1l2 4.5-2 1.5a11 11 0 0 0 6 6l1.5-2 4.5 2-.5 3c-.3 1-1 1.5-2 1.5C8 17.5 2.5 12 2.5 3.5c0-1 .5-1.7 1.5-2z"/></svg></span><span>+1 555 014 2290</span></div>
    <div class="contact"><span class="ring"><svg viewBox="0 0 20 20"><path d="M1 4h18v1.5L10 11 1 5.5z"/><path d="M1 7.5l9 5.5 9-5.5V16H1z"/></svg></span><span>info@carlawinfield.example</span></div>
  </div>
  <div class="foot-nav">Home<span>|</span>Blog<span>|</span>Store<span>|</span>Speaking<span>|</span>Coaching Program<span>|</span>Contact</div>
  <div class="foot-rule"></div>
  <p class="copyright">Copyrights © 2017, Carla Winfield. All rights reserved.</p>
  <div class="social" aria-label="Social links"><span></span><span></span><span></span><span></span></div>
</footer>

</body>
</html>
```